Store Front Signage for an Upscale Cake & Dessert Bakery

We need a design for store front windows. We are a 12 year old bakery specializing in cakes, cupcakes, cookies, pies, and other desserts. We recently moved to a high traffic location.. and we would like to boost our visual presence; we can be seen from the main road but are competing with other businesses for attention. Attached is a photo of our store front with posters but this signage will be for window film for the entire window span. (see the store front to the left of the photo to see the green and yellow as a film example)
Our logo and store sign (not like in photo, that is showing more red) are in shades of pink. The most visible part of the signage is in the upper third to upper half of the 60" panels.
The signs in the window currently say Life's Short. Eat Cake.
We now use Enjoy Life. Eat Cake.
The design should span all the windows and door -- this can be individual panels or one design that covers all panels. I have pink and greys chosen but please DO NOT let this constrain you. The inside of the bakery has grey floors and walls. white cabinetry, black granite countertops. The only thing with color is the baked goods and display cakes, pictures of cakes, the logo and menu and employee shirts.

Target Market(s)

we are located at a busy intersection --- we would like to capture the attention of people in cars as they pass by and entice them to stop in

Font styles to use
Serif
Sans Serif

Colors
d3d3d3
757575
ffffff
e24197
e667a6
eea4c8
f9d9e8

Requirements
Must have
• I would like the design to be easily discernible at the road way that is about 75 feet from store front. If you look at the photos I provide, note that the font size that is easily readable from the road are the ones in the top panes (although the shadow from the building makes them difficult to see -- the best visibility is the top 1/3 of the 60" panels.
Nice to have
• would like to have some non-photo graphics of a cake ( like a birthday cake), tiered cake, cupcakes, and cookies or pie for the panels --- but DO NOT let this constrain you. I need something to grab attention while cars are stopped at the nearby traffic light.
• If this design works well... I will be changing the panel on a seasonal basis
Should not have
• words that cannot be read from a distance.

```html
<!DOCTYPE html>
<html lang="en">
<head>
<meta charset="utf-8">
<title>Rosalind's – Storefront Window Film</title>
<link rel="stylesheet" href="https://fonts.googleapis.com/css2?family=Nunito:wght@700;800;900&family=Zilla+Slab:wght@300;400&display=swap">
<style>
  :root {
    --page: #ececec;
    --frame: #1c1c1c;
    --berry: #990b62;
    --berry-deep: #7e0d51;
    --berry-soft: #c463a6;
    --blush: #f9d9e8;
    --blush-mid: #eea4c8;
    --white: #ffffff;
  }
  * { box-sizing: border-box; margin: 0; padding: 0; }
  html, body { width: 1200px; height: 638px; overflow: hidden; }
  body { background: var(--page); position: relative; }

  .window-film {
    position: absolute;
    left: 30px; top: 33px;
    width: 1140px; height: 572px;
    background: var(--frame);
    padding: 8px;
    display: grid;
    grid-template-columns: 230px 223px 166px 230px 235px;
    grid-template-rows: 158px 288px 92px;
    column-gap: 10px;
    row-gap: 8px;
  }

  .awning-fill {
    background: linear-gradient(180deg, var(--berry) 0%, var(--berry) 68%, var(--berry-deep) 68%, var(--berry-deep) 100%);
  }

  .pane-side {
    position: relative;
    display: flex; flex-direction: column; align-items: center; justify-content: center;
    text-align: center; color: var(--berry);
  }
  .pane-side .damask-fill {
    position: absolute; inset: 0; background: var(--blush);
  }
  .pane-side > *:not(.damask-fill) { position: relative; }
  .feature {
    font-family: "Zilla Slab", Georgia, serif;
    font-weight: 300; font-size: 24px; line-height: 1.0;
  }
  .divider-mark {
    width: 20px; height: 20px; border-radius: 50%;
    background: var(--berry); margin: 14px 0;
  }
  .service-note {
    font-family: "Nunito", Arial, sans-serif;
    font-weight: 800; font-size: 13.5px; line-height: 1.15;
    text-transform: uppercase; margin-top: 6px;
  }

  .pane-brand, .pane-door { display: grid; grid-template-rows: 205px 1fr; }
  .brand-area {
    background: var(--white);
    display: flex; flex-direction: column; align-items: center; justify-content: center;
    color: var(--berry);
  }
  .shop-name {
    display: flex; align-items: center; gap: 8px;
    font-family: "Nunito", Arial, sans-serif;
    font-weight: 900; font-size: 27px; color: var(--berry-deep);
  }
  .shop-name .name-dot {
    width: 14px; height: 14px; border-radius: 50%; background: var(--blush-mid);
  }
  .slogan {
    font-family: "Nunito", Arial, sans-serif;
    font-weight: 800; font-size: 35px; letter-spacing: -0.3px;
    margin-top: 34px;
  }
  .pattern-band { background: var(--berry); }

  .pane-door .brand-area { justify-content: flex-start; padding-top: 48px; }
  .pane-door .shop-name { font-size: 18px; gap: 6px; }
  .pane-door .shop-name .name-dot { width: 10px; height: 10px; }
  .door-rule { width: 46px; height: 2px; background: var(--berry); margin: 22px 0 14px; }
  .hours {
    font-family: "Nunito", Arial, sans-serif;
    font-weight: 800; font-size: 11px; line-height: 1.3;
    text-transform: uppercase; text-align: center; color: var(--berry);
  }

  .kick-stripes {
    background: repeating-linear-gradient(90deg,
      var(--berry-soft) 0 13px, var(--berry) 13px 26px);
  }
</style>
</head>
<body>

<main class="window-film">
  <!-- awning row -->
  <div class="awning-fill" role="img" aria-label="Striped magenta and white scalloped awning illustration"></div>
  <div class="awning-fill" role="img" aria-label="Striped magenta and white scalloped awning illustration"></div>
  <div class="awning-fill" role="img" aria-label="Striped magenta and white scalloped awning illustration"></div>
  <div class="awning-fill" role="img" aria-label="Striped magenta and white scalloped awning illustration"></div>
  <div class="awning-fill" role="img" aria-label="Striped magenta and white scalloped awning illustration"></div>

  <!-- main row -->
  <section class="pane-side">
    <div class="damask-fill" role="img" aria-label="Soft pink damask scroll pattern background"></div>
    <p class="feature">custom<br>cakes</p>
    <div class="divider-mark" role="img" aria-label="Small round flourish ornament"></div>
    <p class="feature">holiday<br>desserts</p>
    <div class="divider-mark" role="img" aria-label="Small round flourish ornament"></div>
    <p class="service-note">Order online<br>rosalindsbakes.com</p>
  </section>

  <section class="pane-brand">
    <div class="brand-area">
      <p class="shop-name"><span class="name-dot"></span>Rosalind's</p>
      <p class="slogan">enjoy life.</p>
    </div>
    <div class="pattern-band" role="img" aria-label="Magenta band with lace border and damask pattern"></div>
  </section>

  <section class="pane-door">
    <div class="brand-area">
      <p class="shop-name"><span class="name-dot"></span>Rosalind's</p>
      <div class="door-rule"></div>
      <p class="hours">Hours:<br>Monday-Saturday<br>9am - 7pm<br>Sunday 11am-5pm</p>
    </div>
    <div class="pattern-band" role="img" aria-label="Magenta band with lace border and damask pattern"></div>
  </section>

  <section class="pane-brand">
    <div class="brand-area">
      <p class="shop-name"><span class="name-dot"></span>Rosalind's</p>
      <p class="slogan">eat cake.</p>
    </div>
    <div class="pattern-band" role="img" aria-label="Magenta band with lace border and damask pattern"></div>
  </section>

  <section class="pane-side">
    <div class="damask-fill" role="img" aria-label="Soft pink damask scroll pattern background"></div>
    <p class="feature">cupcakes<br>galore</p>
    <div class="divider-mark" role="img" aria-label="Small round flourish ornament"></div>
    <p class="feature">sweets and<br>cookies</p>
    <div class="divider-mark" role="img" aria-label="Small round flourish ornament"></div>
    <p class="service-note">Next day pick-up<br>delivery available</p>
  </section>

  <!-- kick panel row -->
  <div class="kick-stripes"></div>
  <div class="kick-stripes"></div>
  <div class="kick-stripes"></div>
  <div class="kick-stripes"></div>
  <div class="kick-stripes"></div>
</main>

</body>
</html>
```